Business Card Design Project - 2 sided

We need a business card design for a card having one business on each side (ie. two businesses on one card). Would like a design that incorporates logo, tagline and normal fields (name, position, address, phone).

Would also like an allowance for small font text along the bottom (text to be determined, but less than 50 characters).

NB. Attached logo for Harbor Quill has two variations - either can be used.

www.harborquill-example.com / www.velmaro-example.com

```html
<!DOCTYPE html>
<html lang="en">
<head>
<meta charset="utf-8">
<title>Harbor Quill / Velmaro – Business Card</title>
<link rel="stylesheet" href="https://fonts.googleapis.com/css2?family=Cinzel:wght@600&family=Open+Sans:wght@400;600;700&display=swap">
<style>
  :root {
    --backdrop: #8a6446;
    --card: #ffffff;
    --navy: #2b2a6b;
    --green: #8cc63f;
    --green-deep: #6a9f3a;
    --green-light: #a9d25e;
    --blue: #2a8fc7;
    --ink: #3d3d3d;
    --muted: #555555;
    --rule: #9a9a9a;
  }
  * { box-sizing: border-box; margin: 0; padding: 0; }
  html, body { width: 1200px; height: 402px; overflow: hidden; }
  body {
    background: var(--backdrop);
    font-family: "Open Sans", Arial, sans-serif;
    color: var(--ink);
    position: relative;
  }
  .card {
    position: absolute;
    top: 56px;
    width: 513px;
    height: 290px;
    background: var(--card);
    overflow: hidden;
    box-shadow: 0 2px 6px rgba(0,0,0,.35);
  }
  .card--harbor { left: 62px; }
  .card--velmaro { left: 626px; }
  .card__band { position: absolute; left: 0; bottom: 0; width: 513px; height: 60px; }
  .card__fineprint {
    position: absolute; left: 0; right: 0; bottom: 14px;
    text-align: center; font-size: 10px; letter-spacing: .5px; color: var(--muted);
  }
  .wordmark {
    position: absolute; left: 0; right: 0;
    display: flex; justify-content: center; align-items: center; gap: 10px;
  }
  .wordmark__dot { border-radius: 50%; }
  .card--harbor .wordmark { top: 86px; }
  .card--harbor .wordmark__name {
    font-family: "Cinzel", Georgia, serif; font-weight: 600;
    font-size: 24px; letter-spacing: 1px; color: var(--navy);
  }
  .card--harbor .wordmark__dot { width: 14px; height: 14px; background: var(--green); }
  .card--velmaro .wordmark { top: 42px; }
  .card--velmaro .wordmark__name {
    font-family: "Open Sans", Arial, sans-serif; font-weight: 600;
    font-size: 48px; letter-spacing: 1px; color: var(--blue); line-height: 1;
  }
  .card--velmaro .wordmark__dot { width: 40px; height: 40px; background: var(--green); }
  .tagline { position: absolute; left: 0; right: 0; text-align: center; }
  .card--harbor .tagline { top: 121px; font-size: 10.5px; font-weight: 600; color: #333; }
  .card--velmaro .tagline { top: 104px; font-size: 15px; letter-spacing: .5px; color: #444; }
  .person {
    position: absolute; left: 0; right: 0; top: 150px; text-align: center;
    font-size: 16px; font-weight: 700; color: var(--navy);
  }
  .person__title { font-size: 13px; font-weight: 400; color: var(--ink); }
  .contact {
    position: absolute; left: 50px; top: 190px;
    display: flex; font-size: 12.5px; line-height: 18px; color: var(--ink);
  }
  .contact__col { padding: 0 10px; border-left: 1px solid var(--rule); }
  .contact__col:first-child { padding-left: 0; border-left: 0; }
  .contact__line { display: flex; align-items: center; gap: 5px; white-space: nowrap; }
  .contact__icon { width: 10px; height: 10px; flex: none; }
</style>
</head>
<body>

<section class="card card--harbor">
  <div class="wordmark"><span class="wordmark__dot"></span><span class="wordmark__name">Harbor Quill</span></div>
  <p class="tagline">Website Translation and Localisation Specialist...</p>
  <p class="person">Your Name <span class="person__title">/ Title</span></p>
  <div class="contact">
    <div class="contact__col">
      <p class="contact__line"><svg class="contact__icon" viewBox="0 0 10 10"><path d="M2 1l2 2-1 1.3c.6 1.2 1.5 2.1 2.7 2.7L7 6l2 2-1.5 1.5C4.5 9 1 5.5.5 2.5z" fill="var(--green)"/></svg>123-456-7890</p>
      <p class="contact__line"><svg class="contact__icon" viewBox="0 0 10 10"><rect x="2.5" y=".5" width="5" height="9" rx="1" fill="var(--green)"/><rect x="3.5" y="1.8" width="3" height="4.5" fill="#fff"/></svg>123-456-7890</p>
    </div>
    <div class="contact__col">
      <p class="contact__line"><svg class="contact__icon" viewBox="0 0 10 10"><rect x=".5" y="2" width="9" height="6.5" fill="var(--green)"/><path d="M.5 2l4.5 3.5L9.5 2" stroke="#fff" fill="none"/></svg>name@website.com</p>
      <p class="contact__line"><svg class="contact__icon" viewBox="0 0 10 10"><circle cx="5" cy="5" r="4.5" fill="var(--green)"/><path d="M.5 5h9M5 .5c-2 2.5-2 6.5 0 9M5 .5c2 2.5 2 6.5 0 9" stroke="#fff" stroke-width=".7" fill="none"/></svg>www.website.com</p>
    </div>
    <div class="contact__col">
      <p class="contact__line">Complex name, Street</p>
      <p class="contact__line">City, State, zip code</p>
    </div>
  </div>
  <svg class="card__band" viewBox="0 0 513 60" preserveAspectRatio="none">
    <path d="M0 18 Q240 0 513 8 L513 60 L0 60Z" fill="var(--green)"/>
    <path d="M0 12 Q220 -4 480 4" stroke="var(--navy)" stroke-width="4" fill="none"/>
  </svg>
  <p class="card__fineprint">xxxxxxxxxxxxxxxxxxxxxxxxxxxxxxxxxxxxxxxxxxxxxxxxxx</p>
</section>

<section class="card card--velmaro">
  <div class="wordmark"><span class="wordmark__dot"></span><span class="wordmark__name">Velmaro</span></div>
  <p class="tagline">Professional SEO Services</p>
  <p class="person">Your Name <span class="person__title">/ Title</span></p>
  <div class="contact">
    <div class="contact__col">
      <p class="contact__line"><svg class="contact__icon" viewBox="0 0 10 10"><path d="M2 1l2 2-1 1.3c.6 1.2 1.5 2.1 2.7 2.7L7 6l2 2-1.5 1.5C4.5 9 1 5.5.5 2.5z" fill="var(--green)"/></svg>123-456-7890</p>
      <p class="contact__line"><svg class="contact__icon" viewBox="0 0 10 10"><rect x="2.5" y=".5" width="5" height="9" rx="1" fill="var(--green)"/><rect x="3.5" y="1.8" width="3" height="4.5" fill="#fff"/></svg>123-456-7890</p>
    </div>
    <div class="contact__col">
      <p class="contact__line"><svg class="contact__icon" viewBox="0 0 10 10"><rect x=".5" y="2" width="9" height="6.5" fill="var(--green)"/><path d="M.5 2l4.5 3.5L9.5 2" stroke="#fff" fill="none"/></svg>name@website.com</p>
      <p class="contact__line"><svg class="contact__icon" viewBox="0 0 10 10"><circle cx="5" cy="5" r="4.5" fill="var(--green)"/><path d="M.5 5h9M5 .5c-2 2.5-2 6.5 0 9M5 .5c2 2.5 2 6.5 0 9" stroke="#fff" stroke-width=".7" fill="none"/></svg>www.website.com</p>
    </div>
    <div class="contact__col">
      <p class="contact__line">Complex name, Street</p>
      <p class="contact__line">City, State, zip code</p>
    </div>
  </div>
  <svg class="card__band" viewBox="0 0 513 60" preserveAspectRatio="none">
    <defs>
      <linearGradient id="velmaroBand" x1="0" x2="1">
        <stop offset="0" stop-color="var(--green-deep)"/>
        <stop offset="1" stop-color="var(--green-light)"/>
      </linearGradient>
    </defs>
    <path d="M0 18 Q240 0 513 8 L513 60 L0 60Z" fill="url(#velmaroBand)"/>
    <path d="M0 12 Q220 -4 480 4" stroke="var(--blue)" stroke-width="4" fill="none"/>
  </svg>
  <p class="card__fineprint">xxxxxxxxxxxxxxxxxxxxxxxxxxxxxxxxxxxxxxxxxxxxxxxxxx</p>
</section>

</body>
</html>
```